Harborview Estates Business Card for Apartment Buildings

Create business cards for resident managers who run apartment buildings. The audience is the public who are searching for apartment rentals, and current residents who live at the apartment building. Key design element will be incorporating the company logo, however, the logo cannot dominate. The building name and manager name are more important than the logo. Current business card design leaves little room for copy, so we may need to reduce the size on the current card to allow for more space for copy.

Target Market(s)

Adults 18-65 years of age, who are looking for an apartment rental, plus current residents who live at our apartment buildings.

Industry/Entity Type

Property Management

Contact Information for Business Card

A major design element will be use of the company logo. Important property and manager contact information must be part of the design. The size of the logo will need to be reduced to make room for building and manager contact copy.

Font styles to use
Sans Serif

Colors
3176b5
000000
959595
ffffff

Requirements
Must have
• 1) Incorporate the company logo.
• 2) Use the company colors (dark blue, black/grey, over white).
• 3) FEATURE THE BUILDING NAME
• 4) FEATURE THE MANAGER NAME
• 5) The company name is less important than BUILDING and MANAGER
• 6) Manager contact information
• **SEE ATTACHED CREATIVE BRIEF**
Nice to have
• 1) Back of card logo watermark
• 2) Ability to write notes on back of carfd
Should not have
• Avoid letting the company logo dominate the card, the building name and manager are more important than the company logo.

```html
<!DOCTYPE html>
<html lang="en">
<head>
<meta charset="utf-8">
<title>Harborview Estates Business Card</title>
<link href="https://fonts.googleapis.com/css2?family=Roboto:wght@400;700;900&display=swap" rel="stylesheet">
<style>
  :root {
    --brand-blue: #3176b5;
    --brand-blue-deep: #1a62a8;
    --brand-black: #000000;
    --brand-grey: #959595;
    --brand-white: #ffffff;
    --canvas-bg: #e9ebee;
    --watermark: #e6e7e9;
  }
  * { box-sizing: border-box; margin: 0; padding: 0; }
  html, body {
    width: 1200px; height: 780px; overflow: hidden;
    background: var(--canvas-bg);
    font-family: "Roboto", Arial, sans-serif;
  }
  .canvas { position: relative; width: 1200px; height: 780px; }
  .card {
    position: absolute; top: 240px;
    width: 520px; height: 300px;
    border-radius: 18px; overflow: hidden;
    background: var(--brand-white);
    box-shadow: 0 10px 28px rgba(0,0,0,.18);
  }
  .card--front { left: 60px; }
  .card--back { left: 620px; background: linear-gradient(160deg, #ffffff 0%, #eef0f2 100%); }
  .card__art { position: absolute; inset: 0; width: 100%; height: 100%; }

  .building {
    position: absolute; top: 28px; left: 34px;
  }
  .building__name {
    font-size: 22px; font-weight: 900; color: var(--brand-black);
    text-transform: uppercase; letter-spacing: .4px;
  }

  .brand {
    position: absolute; top: 32px; right: 34px;
    display: flex; align-items: center; gap: 8px;
  }
  .brand__dot { width: 12px; height: 12px; border-radius: 50%; background: var(--brand-blue); }
  .brand__name {
    font-size: 16px; font-weight: 900; color: var(--brand-blue);
    text-transform: uppercase; letter-spacing: .4px;
  }

  .website {
    position: absolute; right: 30px; top: 160px;
    color: var(--brand-white); font-size: 12.5px; font-weight: 700;
  }

  .manager {
    position: absolute; left: 34px; top: 192px; color: var(--brand-white);
  }
  .manager__name { font-size: 21px; font-weight: 700; text-transform: uppercase; letter-spacing: .3px; }
  .manager__role { font-size: 14px; font-weight: 400; margin-top: 3px; }

  .contact {
    position: absolute; left: 250px; top: 192px; color: var(--brand-white);
    font-size: 12.5px; line-height: 1.45;
  }
  .contact__address { margin-bottom: 6px; }
  .contact__row { display: flex; align-items: center; gap: 7px; }
  .contact__icon { width: 11px; height: 11px; flex: none; }

  .back__mark {
    position: absolute; inset: 0;
    display: flex; align-items: center; justify-content: center;
    font-size: 40px; font-weight: 900; text-transform: uppercase;
    color: var(--watermark); letter-spacing: 1px;
  }
</style>
</head>
<body>
<main class="canvas">

  <section class="card card--front" aria-label="Business card front">
    <svg class="card__art" viewBox="0 0 520 300" preserveAspectRatio="none" aria-hidden="true">
      <defs>
        <linearGradient id="blueBand" x1="0" y1="1" x2="1" y2="0">
          <stop offset="0" stop-color="#1a62a8"/>
          <stop offset="1" stop-color="#3176b5"/>
        </linearGradient>
      </defs>
      <path d="M0,112 C150,190 330,175 520,70 L520,300 L0,300 Z" fill="url(#blueBand)"/>
      <path d="M0,104 C150,182 330,167 520,62" fill="none" stroke="#000000" stroke-width="7"/>
    </svg>

    <div class="building">
      <div class="building__name">The Marina Lofts</div>
    </div>

    <div class="brand">
      <span class="brand__dot"></span>
      <span class="brand__name">Harborview Estates</span>
    </div>

    <div class="website">www.harborviewestates.us</div>

    <div class="manager">
      <div class="manager__name">Daniel Hartley</div>
      <div class="manager__role">Property Manager</div>
    </div>

    <div class="contact">
      <div class="contact__address">2750 Bayline Avenue #B210<br>Portland, OR 97205</div>
      <div class="contact__row">
        <svg class="contact__icon" viewBox="0 0 12 12"><path d="M2 1h3l1 3-1.5 1a6 6 0 0 0 2.5 2.5L8 6l3 1v3a1 1 0 0 1-1 1A9 9 0 0 1 1 2a1 1 0 0 1 1-1z" fill="#fff"/></svg>
        <span>555-214-7730</span>
      </div>
      <div class="contact__row">
        <svg class="contact__icon" viewBox="0 0 12 12"><rect x="3" y="0.5" width="6" height="11" rx="1.2" fill="#fff"/><rect x="4.3" y="2" width="3.4" height="6" fill="#3176b5"/></svg>
        <span>555-318-4092</span>
      </div>
      <div class="contact__row">
        <svg class="contact__icon" viewBox="0 0 12 12"><rect x="0.5" y="2" width="11" height="8" fill="#fff"/><path d="M0.5 2l5.5 4.5L11.5 2" fill="none" stroke="#3176b5" stroke-width="1"/></svg>
        <span>daniel@harborviewestates.us</span>
      </div>
    </div>
  </section>

  <section class="card card--back" aria-label="Business card back">
    <div class="back__mark">Harborview Estates</div>
  </section>

</main>
</body>
</html>
```